Book cover

I am working with my publisher to publish my book They came up with a book cover but I don't like it. I want to see different designs. The book Title is Brightwater the subtitle Ways to Guide Teams Through Storms with Poise, Purpose & Pace by Marlene T. Ostrowski
I want to use my Brand Colors including the blue. I am uploading the covers of my other book. This is a professional leadership book. The publisher will make the cover when providing them a new design. the Brightwater one is one I played with on Canva. I would like more color and to incorporate the blue. I want a spot at the top where I can write a quote. Brightwater is one word in the text so should be the same on the cover. I want the cover to show energy movement and am open to an image too. I am attaching logos for the feel of the brand and brand rgb codes.

```html
<!DOCTYPE html>
<html lang="en">
<head>
<meta charset="utf-8">
<title>Brightwater – Book Cover</title>
<link rel="stylesheet" href="https://fonts.googleapis.com/css2?family=Montserrat:wght@500;700&family=Roboto+Slab:wght@700&family=Saira+Condensed:wght@700&display=swap">
<style>
  :root {
    --teal-deep: #1f7f86;
    --teal: #3aa7ab;
    --teal-light: #8fd0d0;
    --ice: #eef3f3;
    --ice-shade: #d6e3e4;
    --accent-red: #e2452f;
    --title-white: #f4f4f2;
    --band-grey: #5b5b5d;
    --author-white: #f2f2f2;
  }
  * { margin: 0; padding: 0; box-sizing: border-box; }
  html, body {
    width: 980px;
    height: 1200px;
    overflow: hidden;
    background: var(--band-grey);
  }
  .cover {
    position: relative;
    width: 980px;
    height: 1200px;
    overflow: hidden;
  }
  .cover-art {
    position: absolute;
    left: 0; top: 0;
    width: 980px;
    height: 1013px;
    background:
      radial-gradient(ellipse 70% 30% at 30% 4%, var(--ice) 0%, rgba(238,243,243,0) 70%),
      radial-gradient(ellipse 60% 40% at 55% 30%, var(--teal-deep) 0%, rgba(31,127,134,0) 75%),
      radial-gradient(ellipse 85% 35% at 40% 88%, var(--ice) 0%, var(--ice) 45%, rgba(238,243,243,0) 80%),
      linear-gradient(180deg, var(--teal) 0%, var(--teal-deep) 35%, var(--teal-light) 62%, var(--ice-shade) 80%, var(--ice) 100%);
  }
  .tagline {
    position: absolute;
    left: 82px;
    top: 136px;
    font-family: "Montserrat", sans-serif;
    font-weight: 500;
    font-size: 20px;
    line-height: 1.35;
    letter-spacing: 0.9px;
    color: var(--title-white);
    text-transform: uppercase;
  }
  .title {
    position: absolute;
    left: 0; top: 270px;
    width: 980px;
    height: 210px;
    overflow: visible;
  }
  .title text {
    font-family: "Saira Condensed", sans-serif;
    font-weight: 700;
    font-size: 200px;
  }
  .title .title-light { fill: var(--title-white); }
  .title .title-accent { fill: var(--accent-red); }
  .subtitle {
    position: absolute;
    left: 0;
    top: 728px;
    width: 980px;
    text-align: center;
    font-family: "Montserrat", sans-serif;
    font-weight: 700;
    color: var(--accent-red);
  }
  .subtitle .subtitle-lead { display: block; font-size: 29px; line-height: 1.3; }
  .subtitle .subtitle-values { display: block; font-size: 30px; line-height: 1.25; text-transform: uppercase; }
  .author-band {
    position: absolute;
    left: 0;
    top: 1013px;
    width: 980px;
    height: 187px;
    background: var(--band-grey);
    display: flex;
    align-items: center;
    justify-content: center;
  }
  .author {
    font-family: "Roboto Slab", serif;
    font-weight: 700;
    font-size: 38px;
    letter-spacing: 0.5px;
    text-transform: uppercase;
    color: var(--author-white);
    margin-top: -12px;
  }
</style>
</head>
<body>
  <main class="cover">
    <div class="cover-art" role="img" aria-label="Abstract watercolour of flowing teal water and white ice layers"></div>

    <p class="tagline">Brightwater is the essential playbook<br>to turn your uncertainty into possibility</p>

    <svg class="title" viewBox="0 0 980 210" aria-label="Brightwater">
      <defs>
        <filter id="title-lift" x="-5%" y="-10%" width="110%" height="130%">
          <feDropShadow dx="3" dy="5" stdDeviation="3" flood-color="#0b3a3e" flood-opacity="0.55"/>
        </filter>
      </defs>
      <text x="72" y="185" textLength="856" lengthAdjust="spacingAndGlyphs" filter="url(#title-lift)"><tspan class="title-light">BRIGHT</tspan><tspan class="title-accent">WATER</tspan></text>
    </svg>

    <h2 class="subtitle">
      <span class="subtitle-lead">Ways to Guide Teams Through Storms with</span>
      <span class="subtitle-values">Poise, Purpose &amp; Pace</span>
    </h2>

    <footer class="author-band">
      <p class="author">Marlene T. Ostrowski</p>
    </footer>
  </main>
</body>
</html>
```